Tech business card design

We need an amazing business card design for our new business 'Pexla' a marketing tech startup based in Sydney, Australia. We provide an online marketplace for businesses to search and buy advertising media, connect with service providers and learn more about marketing. We wish to communicate 'cool tech', reliability and professionalism and design based around our logo.

Target Market(s)

Business Owners

Contact Information for Business Card

Name
Position
Email Address
Website
Phone Number

Font styles to use
Other font styles liked:
• Avenir & Avenir Next

Colors

Designer to choose colors to be used in the design.

```html
<!DOCTYPE html>
<html lang="en">
<head>
<meta charset="utf-8">
<title>Pexla Business Card</title>
<link href="https://fonts.googleapis.com/css2?family=Figtree:wght@400;700;800&display=swap" rel="stylesheet">
<style>
  :root {
    --stage: #1d1d1e;
    --card-black: #0c0c0d;
    --card-white: #f3f4f8;
    --ink-navy: #17183a;
    --text-light: #f2f2f2;
    --text-muted: #b5b5b8;
    --text-dark: #1a1a1a;
  }
  * { box-sizing: border-box; margin: 0; padding: 0; }
  html, body {
    width: 1200px; height: 1000px; overflow: hidden;
    background: var(--stage);
    font-family: "Figtree", "Avenir Next", Avenir, sans-serif;
  }
  .canvas { position: relative; width: 1200px; height: 1000px; }
  .card {
    position: absolute; left: 290px; width: 620px; height: 354px;
    overflow: hidden; border-radius: 3px;
    box-shadow: 0 18px 40px rgba(0,0,0,.55);
  }
  .card--front { top: 90px; display: flex; }
  .card--back { top: 540px; background: var(--card-black); }

  .front__details {
    width: 45%; background: var(--card-black); color: var(--text-light);
    padding: 118px 0 0 38px;
  }
  .person__name { font-weight: 700; font-size: 26px; line-height: 1; }
  .person__role { font-size: 13px; color: var(--text-muted); margin-top: 4px; }
  .contact-list { list-style: none; margin-top: 22px; }
  .contact-list li {
    display: flex; align-items: center; gap: 18px;
    font-size: 15px; color: var(--text-light); margin-bottom: 16px;
  }
  .contact-list svg { width: 16px; height: 16px; flex: none; fill: var(--text-light); }

  .front__brand {
    flex: 1; background: var(--card-white);
    display: flex; align-items: center; justify-content: center;
  }
  .wordmark {
    font-weight: 800; letter-spacing: -1px; line-height: 1;
    display: inline-flex; align-items: flex-start;
  }
  .wordmark sup { font-size: 11px; font-weight: 800; margin: 8px 0 0 4px; letter-spacing: 0; }
  .front__brand .wordmark { font-size: 86px; color: var(--ink-navy); }

  .back__brand {
    position: absolute; left: 0; right: 0; top: 0; height: 270px;
    display: flex; align-items: center; justify-content: center;
  }
  .back__brand .wordmark { font-size: 96px; color: var(--card-white); }
  .back__band {
    position: absolute; left: 0; right: 0; bottom: 0; height: 84px;
    background: var(--card-white);
    display: flex; align-items: center; justify-content: center;
  }
  .back__url { font-size: 17px; color: var(--text-dark); }
</style>
</head>
<body>
<main class="canvas">
  <section class="card card--front">
    <div class="front__details">
      <h1 class="person__name">Marcus Dale</h1>
      <p class="person__role">Founder, Director</p>
      <ul class="contact-list">
        <li>
          <svg viewBox="0 0 24 24" aria-hidden="true"><path d="M6.6 10.8a15.1 15.1 0 0 0 6.6 6.6l2.2-2.2c.3-.3.7-.4 1-.2 1.1.4 2.3.6 3.6.6.6 0 1 .4 1 1V20c0 .6-.4 1-1 1A17 17 0 0 1 3 4c0-.6.4-1 1-1h3.5c.6 0 1 .4 1 1 0 1.3.2 2.5.6 3.6.1.3 0 .7-.2 1z"/></svg>
          <span>+61 (0)412 555 208</span>
        </li>
        <li>
          <svg viewBox="0 0 24 24" aria-hidden="true"><path d="M2 5h20v14H2zm2 2v.4l8 5.3 8-5.3V7zm0 2.8V17h16V9.8l-8 5.3z"/></svg>
          <span>marcus@pexlamedia.com.au</span>
        </li>
        <li>
          <svg viewBox="0 0 24 24" aria-hidden="true"><path d="M12 2a10 10 0 1 0 0 20 10 10 0 0 0 0-20zm6.9 6h-3a15 15 0 0 0-1.3-3.9A8 8 0 0 1 18.9 8zM12 4c.8 1.2 1.5 2.5 1.9 4h-3.8c.4-1.5 1.1-2.8 1.9-4zM4.3 14a8 8 0 0 1 0-4h3.4a16 16 0 0 0 0 4zm.8 2h3a15 15 0 0 0 1.3 3.9A8 8 0 0 1 5.1 16zm3-8h-3a8 8 0 0 1 4.3-3.9C8.8 5.3 8.4 6.6 8.1 8zM12 20c-.8-1.2-1.5-2.5-1.9-4h3.8c-.4 1.5-1.1 2.8-1.9 4zm2.3-6H9.7a14 14 0 0 1 0-4h4.6a14 14 0 0 1 0 4zm.3 5.9c.6-1.2 1-2.5 1.3-3.9h3a8 8 0 0 1-4.3 3.9zm1.7-5.9a16 16 0 0 0 0-4h3.4a8 8 0 0 1 0 4z"/></svg>
          <span>www.pexlamedia.com.au</span>
        </li>
      </ul>
    </div>
    <div class="front__brand">
      <span class="wordmark">pexla<sup>TM</sup></span>
    </div>
  </section>

  <section class="card card--back">
    <div class="back__brand">
      <span class="wordmark">pexla<sup>TM</sup></span>
    </div>
    <div class="back__band">
      <span class="back__url">www.pexlamedia.com.au</span>
    </div>
  </section>
</main>
</body>
</html>
```